Automotive component supplier needs a business card design

We need a business card design for our company called Velran Global Components Ltd based in the UK. We are a supplier of interior and exterior components to premium car manufacturers such as Corvel Ashby, Hadley Fenn, Marquist and Tavarelli. We would like to see a modern business card design that uses the colour blue.

Target Market(s)

Premium automotive car manufacturers.

Industry/Entity Type

Automotive

Contact Information for Business Card

Company Name : Velran Global Components Limited
Address: 17 Marlow Yard, Upper Heath, Warwick, CV31 8QL, United Kingdom
Web Address : www.velrancomponents-example.co.uk

Font styles to use
Other font styles liked:
• Helvetica

Colors
3176b5
0255a3
85acd3
cfdeed
cee9f5
85cae6
34a6d7
0692cd
9bcb3c

Requirements
Must have
• Clear company logo and a mixture of blue colours.
Nice to have
• A high quality modern image.
Should not have
• Multiple colours.

```html
<!DOCTYPE html>
<html lang="en">
<head>
<meta charset="utf-8">
<title>Velran Global Components – Business Card</title>
<link rel="stylesheet" href="https://fonts.googleapis.com/css2?family=Open+Sans:wght@400;600;700&display=swap">
<style>
  :root {
    --backdrop: #e6e9ec;
    --brand-blue: #0692cd;
    --brand-blue-deep: #0a82bd;
    --map-tone: #0b86c0;
    --accent-green: #9bcb3c;
    --ink: #1c1c1c;
    --white: #ffffff;
  }
  * { box-sizing: border-box; margin: 0; padding: 0; }
  html, body {
    width: 1200px; height: 1000px; overflow: hidden;
    background: var(--backdrop);
    font-family: "Open Sans", Helvetica, Arial, sans-serif;
  }
  .card {
    position: absolute; left: 266px; width: 666px; height: 397px;
    border-radius: 24px; overflow: hidden;
    box-shadow: 0 4px 14px rgba(0,0,0,0.18);
  }
  /* Front */
  .card-front { top: 74px; background: var(--brand-blue); }
  .world-map-area {
    position: absolute; left: 50px; top: 18px; width: 590px; height: 340px;
    border-radius: 60px;
    background: radial-gradient(ellipse at center, var(--map-tone) 0%, rgba(11,134,192,0.35) 60%, rgba(6,146,205,0) 80%);
  }
  .front-wordmark {
    position: absolute; left: 0; right: 0; top: 150px;
    text-align: center; color: var(--white); line-height: 1;
  }
  .front-wordmark .name-main { display: block; font-size: 78px; font-weight: 700; letter-spacing: 1px; }
  .front-wordmark .name-sub { display: block; font-size: 21px; font-weight: 700; letter-spacing: 2px; margin-top: 10px; }
  .front-web {
    position: absolute; left: 0; right: 0; top: 350px; text-align: center;
    color: var(--white); font-size: 16px;
  }
  /* Back */
  .card-back { top: 534px; background: var(--white); }
  .back-wordmark {
    position: absolute; left: 50px; top: 152px; color: var(--brand-blue);
    font-weight: 700; line-height: 1;
  }
  .back-wordmark .name-main { display: block; font-size: 58px; letter-spacing: 1px; }
  .back-wordmark .name-sub { display: block; font-size: 15px; letter-spacing: 1.5px; margin-top: 8px; }
  .contact { position: absolute; left: 345px; top: 84px; color: var(--ink); white-space: nowrap; }
  .contact-name { color: var(--brand-blue-deep); font-weight: 600; font-size: 20px; letter-spacing: 0.5px; }
  .contact-role { font-size: 16px; margin-top: 1px; }
  .contact-address { font-size: 16px; line-height: 24px; margin-top: 16px; }
  .contact-lines { list-style: none; margin-top: 14px; font-size: 16px; line-height: 22.5px; }
  .contact-lines li { display: flex; align-items: center; gap: 6px; }
  .contact-lines svg { width: 15px; height: 13px; fill: var(--brand-blue-deep); flex: none; }
  .footer-band { position: absolute; top: 359px; height: 24px; background: var(--brand-blue); }
  .band-main { left: 0; width: 566px; }
  .band-accent { left: 570px; width: 43px; background: var(--accent-green); border-radius: 3px; }
  .band-end { left: 617px; width: 49px; }
</style>
</head>
<body>
  <section class="card card-front">
    <div class="world-map-area" role="img" aria-label="Faint world map in darker blue behind the company name"></div>
    <div class="front-wordmark">
      <span class="name-main">VELRAN</span>
      <span class="name-sub">GLOBAL COMPONENTS</span>
    </div>
    <p class="front-web">www.velrancomponents-example.co.uk</p>
  </section>

  <section class="card card-back">
    <div class="back-wordmark">
      <span class="name-main">VELRAN</span>
      <span class="name-sub">GLOBAL COMPONENTS</span>
    </div>
    <div class="contact">
      <p class="contact-name">DARREN L. WHITCOMBE</p>
      <p class="contact-role">Managing Director</p>
      <p class="contact-address">Marlow Yard, Upper Heath,<br>Warwick CV31 8QL, UK</p>
      <ul class="contact-lines">
        <li><svg viewBox="0 0 16 14" aria-hidden="true"><path d="M1 5c0-3 14-3 14 0v1h-4V4H5v2H1z M4 7h8l2 6H2z"/></svg>+ 000 000 0000</li>
        <li><svg viewBox="0 0 16 14" aria-hidden="true"><path d="M4 0h8v4H4z M1 5h14v6h-3v3H4v-3H1z M5 9v4h6V9z" fill-rule="evenodd"/></svg>+ 000 000 0000</li>
        <li><svg viewBox="0 0 16 14" aria-hidden="true"><path d="M1 2h14v10H1z M2.5 3.5v7h11v-7L8 8z" fill-rule="evenodd"/></svg>info@velrancomponents-example.co.uk</li>
        <li><svg viewBox="0 0 16 14" aria-hidden="true"><circle cx="7" cy="7" r="6"/><path d="M9 8l6 3-3 1-1 2z" fill="#fff"/></svg>www.velrancomponents-example.co.uk</li>
      </ul>
    </div>
    <div class="footer-band band-main"></div>
    <div class="footer-band band-accent"></div>
    <div class="footer-band band-end"></div>
  </section>
</body>
</html>
```